Industrial B2B Company Seeks Complete Redesign

We manufacture solid/liquid filtration equipment for manufacturers of chemicals, pharmaceuticals and mining products. We will be redesigning our website; our current design is outdated, and a more modern look is desired. Navigation can be improved. Call to action on the header, such as "Start Here". Video on home page. Designer should incorporate colors from our logo, at least the blues, the brown/gold is optional. Existing website can be found at www.BrindleSeparators.com. Also, we do not make water filters and references to water or water-like images should be avoided.
Number of Pages Required
1 page
Look and feel
Each slider illustrates characteristics of the customer's brand and the style your logo design should communicate.

```html
<!DOCTYPE html>
<html lang="en">
<head>
<meta charset="utf-8">
<title>Brindle Separators, Inc.</title>
<link rel="stylesheet" href="https://fonts.googleapis.com/css2?family=Bebas+Neue&family=Montserrat:wght@400;500;600&display=swap">
<style>
:root{
  --blue:#0d8fe6;
  --blue-dark:#0a6fc0;
  --navy:#0a4f90;
  --ink:#222;
  --text:#3a3a3a;
  --pale:#dff0fb;
  --footer:#1c1c1c;
  --field:#1f1f1f;
  --muted:#aaa;
}
*{box-sizing:border-box;margin:0;padding:0}
html,body{width:1200px;height:3219px;overflow:hidden;background:#fff}
body{position:relative;font-family:"Montserrat",sans-serif;color:var(--text)}
.abs{position:absolute}
.head-font{font-family:"Bebas Neue",sans-serif;font-weight:400;text-transform:uppercase;color:var(--ink)}

/* header */
.site-header{position:absolute;left:0;top:0;width:1200px;height:88px;background:#fff;z-index:3}
.brand-tab{position:absolute;left:114px;top:0;width:148px;height:128px;background:#fff;border-radius:0 0 18px 18px;box-shadow:0 4px 12px rgba(0,0,0,.15);display:flex;align-items:center;justify-content:center;text-align:center;font-family:"Bebas Neue",sans-serif;font-size:22px;line-height:1.05;color:var(--blue-dark);text-transform:uppercase}
.nav-link{position:absolute;top:28px;height:33px;line-height:33px;font-family:"Bebas Neue",sans-serif;font-size:20px;color:var(--ink);text-decoration:none;text-transform:uppercase;white-space:nowrap}
.nav-link.active{background:var(--blue);color:#fff;border:1px solid var(--navy);padding:0 11px;line-height:31px}
.search-btn{position:absolute;left:907px;top:31px;width:32px;height:32px;border-radius:50%;background:var(--blue)}
.divider{position:absolute;left:958px;top:28px;width:1px;height:38px;background:#555}
.social-dot{position:absolute;top:30px;width:33px;height:33px;border-radius:50%;border:1.5px solid var(--navy);background:#fff}

/* hero */
.hero{position:absolute;left:0;top:88px;width:1200px;height:647px;background:linear-gradient(180deg,#cfe6f5 0%,#9dcdee 25%,#b8dcf2 55%,#d9ecf8 100%)}
.hero-title{left:113px;top:300px;font-size:64px;line-height:1;white-space:nowrap}
.hero-sub{left:113px;top:380px;font-size:24px;line-height:30px}
.btn{display:inline-flex;align-items:center;justify-content:center;gap:16px;border:2px solid var(--navy);border-radius:30px;background:var(--blue);color:#fff;font-family:"Bebas Neue",sans-serif;text-transform:uppercase;white-space:nowrap}
.hero-btn{left:113px;top:458px;width:149px;height:47px;font-size:21px}
.play{left:113px;top:530px;display:flex;align-items:center;gap:9px;font-family:"Bebas Neue",sans-serif;font-size:23px;color:var(--ink);text-decoration:underline;text-transform:uppercase}
.slider-dot{position:absolute;left:38px;width:14px;height:14px;border-radius:50%;border:1.5px solid #555}
.slider-dot.on{background:var(--blue);border-color:var(--blue)}

/* welcome */
.welcome-title{left:0;width:1200px;top:808px;text-align:center;font-size:46px;line-height:56px}
.intro-col{left:111px;top:952px;width:476px;display:flex;flex-direction:column;gap:14px}
.intro{font-size:14.4px;line-height:24.8px;text-align:justify}
.intro-photo{margin-left:3px;width:473px;height:221px;background:linear-gradient(135deg,#9a9a9a,#5c5c5c 55%,#3a3a3a)}
.feature-col{left:610px;top:942px;width:475px;display:flex;flex-direction:column;gap:16px}
.feature h3{font-family:"Bebas Neue",sans-serif;font-weight:400;font-size:28px;text-transform:uppercase;color:var(--ink);line-height:30px}
.feature p{font-size:14.4px;line-height:24.8px;text-align:justify}
.learn-btn{width:148px;height:47px;font-size:21px;margin-top:10px}

/* products */
.products{position:absolute;left:0;top:1503px;width:1200px;height:587px;background:var(--pale)}
.products-title{left:0;width:1200px;top:1576px;text-align:center;font-size:46px}
.card{position:absolute;top:1666px;width:309px;height:340px;background:#fff;border-radius:14px;box-shadow:0 2px 8px rgba(0,0,0,.12);overflow:hidden;text-align:center}
.card-photo{height:233px}
.card h3{font-family:"Bebas Neue",sans-serif;font-weight:400;font-size:34px;text-transform:uppercase;color:var(--ink);margin-top:14px;line-height:36px;white-space:nowrap}
.card .btn{width:96px;height:28px;font-size:12px;margin-top:6px;gap:8px}

/* contact */
.contact{position:absolute;left:0;top:2090px;width:1200px;height:720px;background:radial-gradient(circle at 30% 30%,#3aa9f0,#1289e0 60%,#0f7fd3)}
.contact-title{left:0;width:1200px;top:2160px;text-align:center;font-size:46px;color:#fff}
.contact-lead{left:240px;width:720px;top:2224px;text-align:center;color:#fff;font-weight:600;font-size:16px;line-height:25px}
.field{position:absolute;height:42px;background:var(--field);color:#e8e8e8;font-size:13.5px;padding:12px 19px;border-radius:2px}
.submit{left:544px;top:2682px;width:112px;height:46px;background:#fff;color:var(--ink);border:2px solid #111;font-size:22px}

/* footer */
.site-footer{position:absolute;left:0;top:2810px;width:1200px;height:409px;background:var(--footer)}
.foot-brand{left:178px;top:2940px;width:150px;text-align:center;font-family:"Bebas Neue",sans-serif;font-size:24px;text-transform:uppercase;line-height:1.05;color:#fff}
.foot-social{position:absolute;top:3052px;width:22px;height:22px;border-radius:50%;background:var(--blue)}
.foot-col{color:#fff}
.foot-col h4{font-family:"Bebas Neue",sans-serif;font-weight:400;font-size:25px;text-transform:uppercase;color:#fff;padding-bottom:6px;border-bottom:2px solid var(--blue);display:inline-block;width:52px;white-space:nowrap;margin-bottom:14px}
.foot-col a{display:block;color:#fff;text-decoration:none;font-size:13px;font-weight:500;line-height:26px;text-transform:uppercase}
.contact-row{position:absolute;left:830px;display:flex;gap:18px;align-items:flex-start;color:#fff}
.contact-row .ico{width:34px;height:34px;flex:none}
.contact-row small{display:block;color:var(--muted);font-size:13px}
.contact-row span{font-size:13px;line-height:19px;color:#fff}
.foot-line{left:113px;top:3144px;width:978px;height:1px;background:var(--blue)}
.copyright{left:0;width:1200px;top:3173px;text-align:center;font-size:14.5px;color:#fff}
.to-top{left:1117px;top:3132px;width:40px;height:40px;border-radius:8px;background:var(--blue)}
</style>
</head>
<body>

<header class="site-header">
  <div class="brand-tab">Brindle<br>Separators</div>
  <nav>
    <a class="nav-link active" href="#" style="left:401px">Home</a>
    <a class="nav-link" href="#" style="left:494px">About Us</a>
    <a class="nav-link" href="#" style="left:604px">Products &amp; Services</a>
    <a class="nav-link" href="#" style="left:798px">Contact Us</a>
  </nav>
  <div class="search-btn" aria-label="Search">
    <svg width="32" height="32" viewBox="0 0 32 32"><circle cx="15" cy="15" r="5" fill="none" stroke="#fff" stroke-width="2"/><line x1="19" y1="19" x2="22" y2="22" stroke="#fff" stroke-width="2"/></svg>
  </div>
  <div class="divider"></div>
  <div class="social-dot" style="left:971px" aria-label="Social link"></div>
  <div class="social-dot" style="left:1013px" aria-label="Social link"></div>
  <div class="social-dot" style="left:1051px" aria-label="Social link"></div>
</header>

<section class="hero" role="img" aria-label="Hero background with rising bubbles in blue liquid"></section>
<span class="slider-dot" style="top:366px"></span>
<span class="slider-dot on" style="top:389px"></span>
<span class="slider-dot" style="top:411px"></span>
<span class="slider-dot" style="top:433px"></span>
<h1 class="abs head-font hero-title">Brindle Separators, Inc.</h1>
<p class="abs head-font hero-sub">Liquid filtration: exceptional quality,<br>unparalleled performance</p>
<a class="abs btn hero-btn">Start Here <span>&gt;</span></a>
<div class="abs play">
  <svg width="46" height="46" viewBox="0 0 46 46"><circle cx="23" cy="23" r="21" fill="none" stroke="#0d8fe6" stroke-width="3"/><circle cx="23" cy="23" r="15" fill="#fff"/><polygon points="18,13 33,23 18,33" fill="#0d8fe6"/></svg>
  Play Video
</div>

<h2 class="abs head-font welcome-title">Welcome to Brindle Separators®:<br>your partner in solid-liquid separation</h2>
<div class="abs intro-col">
  <p class="intro">At Brindle Separators, we've been setting the standard in liquid filtration for nearly a century. As a leading manufacturer, we pride ourselves on crafting high-quality, long-lasting filtration equipment tailored to meet the unique needs of our customers. With each of our products our goal is to provide you with unwavering reliability, predictability, superior service and exceptional returns on your investment that span decades.</p>
  <div class="intro-photo" role="img" aria-label="Historic black and white photo of the original brick factory building"></div>
</div>
<div class="abs feature-col">
  <div class="feature">
    <h3>Innovation Pioneers</h3>
    <p>Our legacy is one of innovation. Almost a century ago, Brindle Separators pioneered the first modern-style horizontal plate filter, introduced the first residential and field-use filters, and even revolutionized the cooking oil filtration process. These and countless other groundbreaking innovations have defined our iconic status and continue to fuel our passion for solving filtration challenges.</p>
  </div>
  <div class="feature">
    <h3>Engineering Expertise at Your Service</h3>
    <p>With our ~100 year history, Brindle Separators has accumulated unparalleled engineering expertise in industrial liquid filtration. We stand ready to deliver the best possible solution for your unique filtration challenges. Whatever your application goals may be, Brindle can work closely with you to develop a customized, optimal solution.</p>
  </div>
  <a class="btn learn-btn">Learn More <span>&gt;</span></a>
</div>

<section class="products"></section>
<h2 class="abs head-font products-title">Our Products</h2>
<article class="card" style="left:111px">
  <div class="card-photo" role="img" aria-label="Close-up of woven white filter media fabric" style="background:linear-gradient(135deg,#d8d8d8,#f2f2f2 50%,#bdbdbd)"></div>
  <h3>Filter Media</h3>
  <a class="btn">Learn More <span>&gt;</span></a>
</article>
<article class="card" style="left:446px">
  <div class="card-photo" role="img" aria-label="Stainless steel pressure filter vessel on wheeled frame" style="background:linear-gradient(180deg,#cfe6f5,#7bbde8 60%,#2e8fd6)"></div>
  <h3>Pressure &amp; Vacuum Filters</h3>
  <a class="btn">Learn More <span>&gt;</span></a>
</article>
<article class="card" style="left:780px">
  <div class="card-photo" role="img" aria-label="Consultant in a suit gesturing across a desk" style="background:linear-gradient(135deg,#f4f5f7,#cdd2da 55%,#3b4456)"></div>
  <h3>Process Consulting</h3>
  <a class="btn">Learn More <span>&gt;</span></a>
</article>

<section class="contact" role="img" aria-label="Blue rippled liquid surface background"></section>
<h2 class="abs head-font contact-title">Contact Us</h2>
<p class="abs contact-lead">Whether your question is about pricing, product support, process or application needs or other filtration related question please feel free to reach out to us.</p>
<div class="field" style="left:273px;top:2294px;width:653px">Full Name</div>
<div class="field" style="left:273px;top:2354px;width:318px">E-mail</div>
<div class="field" style="left:608px;top:2354px;width:318px">Phone</div>
<div class="field" style="left:273px;top:2414px;width:653px">Subject</div>
<div class="field" style="left:273px;top:2474px;width:653px">Address</div>
<div class="field" style="left:273px;top:2534px;width:653px;height:125px">Enter Your Message</div>
<a class="abs btn submit">Submit <span>&gt;</span></a>

<footer class="site-footer"></footer>
<div class="abs foot-brand">Brindle<br>Separators</div>
<span class="foot-social" style="left:194px" aria-label="Social link"></span>
<span class="foot-social" style="left:242px" aria-label="Social link"></span>
<span class="foot-social" style="left:296px" aria-label="Social link"></span>
<div class="abs foot-col" style="left:412px;top:2888px">
  <h4>Links</h4>
  <a>Home</a><a>About Us</a><a>Products &amp; Services</a><a>Contact Us</a>
</div>
<div class="abs foot-col" style="left:642px;top:2888px">
  <h4>Support</h4>
  <a>Resources</a><a>Team</a><a>About Us</a><a>Careers</a><a>Our Values</a>
</div>
<div class="abs foot-col" style="left:838px;top:2888px"><h4>Contact Us</h4></div>
<div class="contact-row" style="top:2940px">
  <svg class="ico" viewBox="0 0 34 34"><circle cx="17" cy="17" r="17" fill="#3a3a3a"/><path d="M17 9a5 5 0 0 0-5 5c0 4 5 10 5 10s5-6 5-10a5 5 0 0 0-5-5z" fill="#0d8fe6"/><circle cx="17" cy="14" r="2" fill="#3a3a3a"/></svg>
  <div><small>Address</small><span>48 Harlan Ridge Road<br>Millbrook, Texas 75990-2210</span></div>
</div>
<div class="contact-row" style="top:3012px">
  <svg class="ico" viewBox="0 0 34 34"><circle cx="17" cy="17" r="17" fill="#3a3a3a"/><path d="M11 10l4 0 1 4-2 2a10 10 0 0 0 4 4l2-2 4 1 0 4c-8 1-14-5-13-13z" fill="#0d8fe6"/></svg>
  <div><small>Call Us</small><span>(555) 014-2290</span></div>
</div>
<div class="contact-row" style="top:3072px">
  <svg class="ico" viewBox="0 0 34 34"><circle cx="17" cy="17" r="17" fill="#3a3a3a"/><rect x="9" y="12" width="16" height="11" fill="#0d8fe6"/><path d="M9 12l8 6 8-6" fill="none" stroke="#3a3a3a" stroke-width="1.5"/></svg>
  <div><small>Email</small><span>sales@brindleseparators.com</span></div>
</div>
<div class="abs foot-line"></div>
<p class="abs copyright">©2024. All rights reserved.</p>
<div class="abs to-top" aria-label="Back to top">
  <svg width="40" height="40" viewBox="0 0 40 40"><path d="M15 22l5-5 5 5" fill="none" stroke="#fff" stroke-width="2"/></svg>
</div>

</body>
</html>
```